KV HOLDING Business Cards

I need business cards for "KV Holding group LLC" doublesided... logo on the back (also include logo on front)
logo attached to project... i have jpg up..
Company Info:
827 North Cadwell Avenue, Suite 4B
Chicago, Illinois 60654
facsimile 312-481-2075 (list fax, address, website on all cards.)
www.kvholdinggroup.example
Three different people on cards:
Darnell P. Okafor, CPA MST
Principal
ofc 312-481-3900
mobile 312-204-7751
darnellpokafor@kvholdinggroup.example
Hollis T. Brennecke, CPA MST
Principal
hollistbrennecke@kvholdinggroup.example
mobile 708-539-1184
ofc 312-481-3900
Conrad M Pavlik
Principal
ofc 312-481-3900
no mobile
conradmpavlik@kvholdinggroup.example
I have multiple projects listed.. see below:
Business cards for amber gate ventures llc
letterhead
envelopes
Business cards for KV Holding LLC
letterhead
envelopes
Target Market(s)
rich people
Industry/Entity Type
Business
Look and feel
Each slider illustrates characteristics of the customer's brand and the style your logo design should communicate.

```html
<!DOCTYPE html>
<html lang="en">
<head>
<meta charset="utf-8">
<title>KV Holding Group LLC – Business Cards</title>
<link href="https://fonts.googleapis.com/css2?family=Arimo:wght@400;700&display=swap" rel="stylesheet">
<style>
  :root{
    --navy:#1d3f7c;
    --navy-deep:#163467;
    --ink:#1c3a73;
    --grey:#b9bcc2;
    --grey-light:#e4e5e8;
    --paper:#ffffff;
    --backdrop:#e9eaed;
  }
  *{margin:0;padding:0;box-sizing:border-box}
  html,body{width:1200px;height:1068px;overflow:hidden;background:var(--backdrop)}
  body{font-family:"Arimo",Arial,sans-serif;color:var(--ink);position:relative}
  .card{
    position:absolute;top:371px;width:560px;height:326px;background:var(--paper);
    overflow:hidden;box-shadow:0 4px 18px rgba(0,0,0,.12);
  }
  .card--front{left:30px}
  .card--back{left:610px}

  .mark{border-radius:50%;background:var(--navy)}
  .wordmark{font-family:"Arimo",Arial,sans-serif;font-weight:400;color:var(--navy);letter-spacing:.06em;text-transform:uppercase;white-space:nowrap}

  /* front */
  .front-mark{position:absolute;left:240px;top:26px;width:80px;height:80px}
  .front-wordmark{position:absolute;left:0;right:0;top:122px;text-align:center;font-size:25px}
  .address{position:absolute;left:0;right:0;top:178px;text-align:center;font-weight:700;font-size:17.5px;line-height:24px}
  .front-waves{position:absolute;left:0;bottom:0;width:560px;height:110px}
  .band-text{position:absolute;bottom:16px;color:#fff;font-weight:700;font-size:18px;display:flex;align-items:center;gap:8px}
  .band-text--fax{left:36px}
  .band-text--web{right:28px}

  /* back */
  .back-mark{position:absolute;left:30px;top:18px;width:64px;height:64px}
  .back-wordmark{position:absolute;left:112px;top:18px;font-size:22px}
  .office{position:absolute;left:0;right:0;top:46px;padding-left:60px;text-align:center;font-size:15px}
  .person{position:absolute;left:0;right:0;padding-left:80px;text-align:center;font-size:14.5px;line-height:19px}
  .person .name{font-weight:700;font-size:16px}
  .person--1{top:96px}
  .person--2{top:184px}
  .person--3{top:260px}
  .divider{position:absolute;left:0;width:560px;height:26px}
  .divider--1{top:160px}
  .divider--2{top:238px}
</style>
</head>
<body>

<section class="card card--front" aria-label="Business card front">
  <div class="mark front-mark" aria-hidden="true"></div>
  <div class="wordmark front-wordmark">KV Holding Group LLC</div>
  <p class="address">827 North Cadwell Avenue, Suite 4B<br>Chicago, Illinois 60654</p>
  <svg class="front-waves" viewBox="0 0 560 110" preserveAspectRatio="none" aria-hidden="true">
    <defs>
      <linearGradient id="swoosh" x1="0" x2="1">
        <stop offset="0" stop-color="#9da1a8"/>
        <stop offset=".6" stop-color="#d2d4d8"/>
        <stop offset="1" stop-color="#f2f2f4"/>
      </linearGradient>
    </defs>
    <path d="M0 22 C160 8 360 18 560 62 L560 66 C360 30 170 24 0 40 Z" fill="url(#swoosh)"/>
    <path d="M0 42 C170 26 360 34 560 70 L560 110 L0 110 Z" fill="var(--navy)"/>
  </svg>
  <div class="band-text band-text--fax">
    <svg width="22" height="20" viewBox="0 0 22 20" aria-hidden="true">
      <rect x="5" y="1" width="11" height="7" fill="none" stroke="#fff" stroke-width="1.6"/>
      <rect x="1" y="7" width="20" height="12" rx="2" fill="#fff"/>
      <rect x="4" y="10" width="7" height="6" fill="var(--navy)"/>
      <rect x="13" y="10" width="2" height="2" fill="var(--navy)"/>
      <rect x="16" y="10" width="2" height="2" fill="var(--navy)"/>
      <rect x="13" y="14" width="2" height="2" fill="var(--navy)"/>
      <rect x="16" y="14" width="2" height="2" fill="var(--navy)"/>
    </svg>
    <span>312-481-2075</span>
  </div>
  <div class="band-text band-text--web">www.kvholdinggroup.example</div>
</section>

<section class="card card--back" aria-label="Business card back">
  <div class="mark back-mark" aria-hidden="true"></div>
  <div class="wordmark back-wordmark">KV Holding Group LLC</div>
  <p class="office">Office 312-481-3900</p>

  <div class="person person--1">
    <p><span class="name">Darnell P. Okafor</span>, CPA MST, Principal</p>
    <p>mobile 312-204-7751</p>
    <p>darnellpokafor@kvholdinggroup.example</p>
  </div>

  <svg class="divider divider--1" viewBox="0 0 560 26" preserveAspectRatio="none" aria-hidden="true">
    <path d="M0 14 C180 2 380 4 560 14 L560 16 C380 8 180 8 0 22 Z" fill="var(--grey)"/>
  </svg>

  <div class="person person--2">
    <p><span class="name">Hollis T. Brennecke</span>, CPA MST, Principal</p>
    <p>hollistbrennecke@kvholdinggroup.example</p>
    <p>mobile 708-539-1184</p>
  </div>

  <svg class="divider divider--2" viewBox="0 0 560 26" preserveAspectRatio="none" aria-hidden="true">
    <path d="M0 14 C180 2 380 4 560 14 L560 16 C380 8 180 8 0 22 Z" fill="var(--grey)"/>
  </svg>

  <div class="person person--3">
    <p><span class="name">Conrad M Pavlik</span>, Principal</p>
    <p>conradmpavlik@kvholdinggroup.example</p>
  </div>
</section>

</body>
</html>
```